Luxury free range egg pack for eggs with golden orange yolks

We are looking for a new faced egg pack for one of our brands called Meadow Crest which is free range eggs with golden yolks.
This will be for a more up market target audience.

Target Market(s)

Luxury egg purchase

Industry/Entity Type

Egg production

Font styles to use
Decorative
Script

Colors
F0912C
F2A743
F7CA91
FBE8D2
FDF5EE

Requirements
Must have
• Orange or gold colouring in place in the theme

```html
<!DOCTYPE html>
<html lang="en">
<head>
<meta charset="utf-8">
<title>Free Range Egg – Pack Label</title>
<link rel="stylesheet" href="https://fonts.googleapis.com/css2?family=Cinzel+Decorative:wght@700;900&family=Cormorant+Garamond:ital,wght@0,700;1,700&display=swap">
<style>
  :root {
    --backdrop: #FDF5EE;
    --maroon: #6B1F2B;
    --maroon-deep: #521621;
    --gold: #C9A45C;
    --gold-light: #E9D6A9;
    --gold-pale: #F4E7C6;
    --bronze: #B5774F;
    --bronze-light: #C98D64;
    --emblem-tone: #BF8560;
  }
  html, body {
    margin: 0;
    padding: 0;
    width: 750px;
    height: 1200px;
    overflow: hidden;
    background: var(--backdrop);
  }
  .canvas {
    position: relative;
    width: 750px;
    height: 1200px;
  }
  .pack-label {
    position: absolute;
    left: 25px;
    top: 375px;
    width: 700px;
    height: 450px;
  }
  .title {
    font-family: "Cinzel Decorative", serif;
    font-weight: 900;
    font-size: 20px;
    fill: var(--gold-pale);
  }
  .tagline {
    font-family: "Cormorant Garamond", serif;
    font-style: italic;
    font-weight: 700;
    font-size: 14px;
    fill: var(--gold-pale);
  }
  .grade {
    font-family: "Cormorant Garamond", serif;
    font-style: italic;
    font-weight: 700;
    font-size: 15px;
    fill: var(--maroon-deep);
  }
  .count {
    font-family: "Cinzel Decorative", serif;
    font-weight: 900;
    font-size: 24px;
    fill: var(--gold-pale);
  }
  .size {
    font-family: "Cinzel Decorative", serif;
    font-weight: 700;
    font-size: 14px;
    fill: var(--gold-pale);
  }
</style>
</head>
<body>
<main class="canvas">
  <svg class="pack-label" viewBox="0 0 700 450" xmlns="http://www.w3.org/2000/svg">
    <defs>
      <linearGradient id="panel-fill" x1="0" y1="0" x2="1" y2="1">
        <stop offset="0" stop-color="#F1E2BC"/>
        <stop offset="0.5" stop-color="#E2C98F"/>
        <stop offset="1" stop-color="#F1E2BC"/>
      </linearGradient>
      <radialGradient id="oval-fill" cx="0.45" cy="0.35" r="0.7">
        <stop offset="0" stop-color="#C98D64"/>
        <stop offset="1" stop-color="#B5774F"/>
      </radialGradient>
    </defs>

    <g class="band">
      <rect x="2" y="25" width="696" height="390" rx="28" fill="var(--gold)"/>
      <rect x="10" y="33" width="680" height="374" rx="22" fill="var(--maroon)"/>
      <rect x="28" y="51" width="644" height="338" rx="14" fill="var(--gold)"/>
      <rect x="33" y="56" width="634" height="328" rx="12" fill="url(#panel-fill)" role="img" aria-label="Fine diagonal gold pin-stripe texture"/>
    </g>

    <g class="side-ornaments">
      <rect x="70" y="140" width="60" height="150" rx="30" fill="var(--maroon)" opacity="0.22" role="img" aria-label="Maroon flourish ornament"/>
      <rect x="570" y="140" width="60" height="150" rx="30" fill="var(--maroon)" opacity="0.22" role="img" aria-label="Maroon flourish ornament"/>
    </g>

    <g class="seal">
      <ellipse cx="350" cy="225" rx="160" ry="222" fill="var(--gold)"/>
      <ellipse cx="350" cy="225" rx="152" ry="214" fill="var(--maroon)"/>
      <ellipse cx="350" cy="225" rx="142" ry="204" fill="none" stroke="var(--gold-light)" stroke-width="12" stroke-dasharray="14 12"/>
      <ellipse cx="350" cy="225" rx="130" ry="192" fill="var(--gold)"/>
      <ellipse cx="350" cy="225" rx="124" ry="186" fill="var(--maroon)"/>
      <ellipse cx="350" cy="225" rx="118" ry="180" fill="url(#oval-fill)"/>

      <ellipse class="emblem" cx="350" cy="150" rx="78" ry="88" fill="var(--emblem-tone)" role="img" aria-label="Decorative emblem area"/>

      <text class="title" x="350" y="272" text-anchor="middle" textLength="200" lengthAdjust="spacingAndGlyphs">Free Range Egg</text>
      <text class="tagline" x="350" y="296" text-anchor="middle">With Golden Orange Yolks</text>
      <line x1="298" y1="307" x2="402" y2="307" stroke="var(--maroon-deep)" stroke-width="1"/>
      <text class="grade" x="350" y="327" text-anchor="middle">Class A</text>
      <line x1="318" y1="335" x2="382" y2="335" stroke="var(--gold-pale)" stroke-width="1"/>
      <text class="count" x="350" y="362" text-anchor="middle">6</text>
      <text class="size" x="350" y="382" text-anchor="middle">Large Egg</text>
    </g>
  </svg>
</main>
</body>
</html>
```